Brochure and Business Card design

I am looking for a high end, elegant A4, 4 page brochure booklet to convey our products to clientele that will be visiting a luxury display showroom.

Harrowgate Locks and Grilles is a Australian security provider, and we supply high end products from reputable brands.
The brochure will be directed to clients building a new home with a partnered building company and will be accompanied with display boards of our products.

I am providing files of a document we have put together with the relevant information and some images to help along the way, we are not bound by the layout or style it has been drawn up and we wish to give you complete creative freedom putting the peaces together. I have also provided the files for our logo in two different colours, and a picture of a brochure we love the look of.

If you have any suggestions, we can likely come up with further images etc if it will help or even if you feel some should be removed, we are open to that also

Target Market(s)

Young familys, people building new luxury homes, proffesionals, home owners

Industry/Entity Type

Business

Font styles to use
Serif
Sans Serif

Requirements
Must have
• All 8 pages
Should not have
• Not really a fan of reds and similar.

```html
<!DOCTYPE html>
<html lang="en">
<head>
<meta charset="utf-8">
<title>Harrowgate Locks and Grilles – Brochure Spreads</title>
<link href="https://fonts.googleapis.com/css2?family=Raleway:wght@300;400;600&family=Open+Sans:wght@400;600;700&display=swap" rel="stylesheet">
<style>
:root{
  --bg:#bdbdbd;
  --paper:#ffffff;
  --blue:#2b86c8;
  --blue-dark:#1f6faa;
  --green:#8cc63f;
  --ink:#4a4a4a;
  --muted:#8a8a8a;
  --rule:#e3e3e3;
  --photo-grey:#8f9396;
}
*{box-sizing:border-box;margin:0;padding:0}
html,body{width:1200px;height:754px;overflow:hidden;background:var(--bg)}
body{font-family:"Open Sans",sans-serif;color:var(--ink)}
.board{display:grid;grid-template-columns:600px 600px;grid-template-rows:377px 377px;width:1200px;height:754px}
.cell{position:relative;display:flex;align-items:center;justify-content:center}
.spread{display:flex;width:540px;height:190px;box-shadow:0 6px 14px rgba(0,0,0,.22)}
.page{position:relative;width:270px;height:190px;background:var(--paper);overflow:hidden}
.page.left{border-right:1px solid var(--rule)}
.body-text{font-size:4.6px;line-height:6.4px;color:var(--muted)}
.title{font-family:"Raleway",sans-serif;font-weight:300;color:var(--blue);position:absolute}
.sub{font-size:5px;font-weight:700;color:var(--green);text-transform:uppercase;letter-spacing:.2px}
.ph{position:absolute}
.brand{font-family:"Open Sans",sans-serif;font-weight:700;color:#555;position:absolute;display:flex;align-items:center;gap:4px;letter-spacing:.5px}
.brand .dot{width:7px;height:7px;border-radius:50%;background:var(--green)}

/* cover */
.band{position:absolute;left:0;right:0;top:70px;height:48px;background:var(--blue)}
.band p{color:#fff;font-size:4.6px;line-height:6.5px;text-align:center;padding:9px 26px 0}
.enquiries{position:absolute;left:0;right:0;top:132px;text-align:center}
.enquiries .label{font-size:5px;color:var(--green);font-weight:600}
.enquiries .contact{font-size:4.4px;color:var(--ink);margin-top:4px}
.enquiries .web{font-size:7px;color:var(--blue);font-weight:700;margin-top:4px}
.copyright{position:absolute;left:0;right:0;bottom:10px;text-align:center;font-size:3.6px;color:var(--muted)}
.front-band{position:absolute;left:0;top:70px;width:40px;height:48px;background:var(--blue)}
.green-strip{position:absolute;right:0;top:60px;width:14px;height:62px;background:var(--green)}

/* lists */
.item{position:absolute;display:flex;align-items:center;gap:5px}
.item .thumb{width:14px;height:14px;background:#d6d9dc;border-radius:1px}
.item span{font-size:4.2px;color:var(--ink);line-height:5.5px}
.note{position:absolute;background:var(--blue);color:#fff;font-size:4.6px;padding:3px 6px}
.row{position:absolute;left:14px;right:14px;display:flex;gap:6px;align-items:flex-start;border-bottom:1px solid var(--rule);padding-bottom:4px}
.row .thumb{width:22px;height:16px;background:#dde0e3;flex:none}
.row h4{font-size:5px;color:var(--blue);font-weight:600}
.feature{position:absolute;left:12px;right:12px;display:flex;gap:8px}
.feature .icon{width:30px;height:18px;flex:none}
.feature h4{font-size:5px;color:var(--green);font-weight:700}
</style>
</head>
<body>
<main class="board">

  <!-- Cover spread -->
  <section class="cell">
    <div class="spread">
      <article class="page left">
        <div class="brand" style="left:96px;top:42px;font-size:7px"><span class="dot"></span>HARROWGATE</div>
        <div class="band"><p>Harrowgate Locks and Grilles is an Australian owned security provider supplying premium products for new homes.<br><br>Speak with our team for a tailored consultation.</p></div>
        <div class="enquiries">
          <div class="label">For all Enquiries</div>
          <div class="contact">Email: hello@harrowgatelocks.com.au &nbsp;|&nbsp; Phone: 1300 555 014</div>
          <div class="web">www.harrowgatelocks.com.au</div>
        </div>
        <div class="copyright">This document and all content is copyright of Harrowgate Locks and Grilles.</div>
      </article>
      <article class="page">
        <div class="front-band"></div>
        <div class="ph" role="img" aria-label="Photo of an intercom panel on a dark wall" style="left:40px;top:64px;width:58px;height:60px;background:linear-gradient(160deg,#6c6e70,#3e4042)"></div>
        <div class="ph" role="img" aria-label="Photo of a modern two storey home" style="left:100px;top:64px;width:64px;height:60px;background:linear-gradient(180deg,#9fc2e0,#a08d78)"></div>
        <div class="ph" role="img" aria-label="Photo of a home facade with security screens" style="left:166px;top:64px;width:68px;height:60px;background:linear-gradient(180deg,#c7d6e2,#6d6a66)"></div>
        <div class="green-strip"></div>
        <div class="brand" style="right:16px;top:146px;font-size:10px"><span class="dot"></span>HARROWGATE</div>
      </article>
    </div>
  </section>

  <!-- Alarm / Intercom spread -->
  <section class="cell">
    <div class="spread">
      <article class="page left">
        <h2 class="title" style="left:14px;top:12px;font-size:13px">Alarm Systems</h2>
        <p class="body-text ph" style="left:14px;top:32px;width:105px">Protect your new home with a monitored alarm system designed around your family and lifestyle.</p>
        <div class="ph" role="img" aria-label="Photo of an alarm keypad on a wall" style="left:128px;top:10px;width:130px;height:46px;background:linear-gradient(120deg,#dcdcdc,#6e6e6e)"></div>
        <div class="sub ph" style="left:14px;top:66px">Popular Upgrades</div>
        <div class="item" style="left:14px;top:78px"><i class="thumb"></i><span>Touch Keypad</span></div>
        <div class="item" style="left:70px;top:78px"><i class="thumb"></i><span>Motion Sensor</span></div>
        <div class="item" style="left:14px;top:98px"><i class="thumb"></i><span>Smoke Detector</span></div>
        <div class="item" style="left:70px;top:98px"><i class="thumb"></i><span>Door Reed</span></div>
        <div class="item" style="left:14px;top:118px"><i class="thumb"></i><span>Remote Fob</span></div>
        <div class="note" style="left:128px;top:62px;width:130px">Every system is installed by licensed technicians.</div>
      </article>
      <article class="page">
        <h2 class="title" style="left:14px;top:10px;font-size:12px">Intercom</h2>
        <p class="body-text ph" style="left:14px;top:28px;width:130px">Know who is at the door before you open it, from any room in the house.</p>
        <div class="ph" role="img" aria-label="Photo of a video intercom in a bright hallway" style="left:152px;top:8px;width:108px;height:44px;background:linear-gradient(120deg,#eef1f4,#c9a98a)"></div>
        <div class="row" style="top:58px;right:110px"><i class="thumb"></i><div><h4>7in Colour Video Intercom</h4><p class="body-text">Hands free with door release and memory.</p></div></div>
        <div class="row" style="top:88px;right:110px"><i class="thumb"></i><div><h4>4in Colour Video Intercom</h4><p class="body-text">Hands free with door release and memory.</p></div></div>
        <div class="row" style="top:118px;right:110px"><i class="thumb"></i><div><h4>Audio Only Intercom</h4><p class="body-text">Hands free with door release and memory.</p></div></div>
        <div class="sub ph" style="left:172px;top:60px">Popular Upgrades</div>
        <div class="item" style="left:172px;top:72px"><i class="thumb"></i><span>Extra Indoor Monitor</span></div>
        <div class="item" style="left:172px;top:94px"><i class="thumb"></i><span>Camera Door Station</span></div>
        <div class="item" style="left:172px;top:116px"><i class="thumb"></i><span>Smartphone App</span></div>
      </article>
    </div>
  </section>

  <!-- Mesh spread -->
  <section class="cell">
    <div class="spread">
      <article class="page left">
        <div class="ph" role="img" aria-label="Close-up photo of a steel mesh security door" style="left:40px;top:0;width:230px;height:70px;background:linear-gradient(100deg,#f2f2f2,#7a7a7a 60%,#2f2f2f)"></div>
        <h2 class="title" style="left:110px;top:82px;font-size:12px">Why Stronghold Mesh?</h2>
        <p class="body-text ph" style="left:110px;top:102px;width:140px">Stainless steel mesh screens that keep insects out and let the breeze in without spoiling your view.</p>
      </article>
      <article class="page">
        <div class="feature" style="top:22px"><svg class="icon" viewBox="0 0 30 18"><polygon points="2,16 15,3 28,16" fill="#cfd2d5"/></svg><div><h4>Tough Mesh</h4><p class="body-text">Woven steel resists cuts and impact while staying light.</p></div></div>
        <div class="feature" style="top:58px"><svg class="icon" viewBox="0 0 30 18"><polygon points="2,16 15,3 28,16" fill="#cfd2d5"/></svg><div><h4>Durable</h4><p class="body-text">Woven steel resists cuts and impact while staying light.</p></div></div>
        <div class="feature" style="top:94px"><svg class="icon" viewBox="0 0 30 18"><polygon points="2,16 15,3 28,16" fill="#cfd2d5"/></svg><div><h4>Clear View</h4><p class="body-text">Woven steel resists cuts and impact while staying light.</p></div></div>
        <div class="feature" style="top:130px"><svg class="icon" viewBox="0 0 30 18"><polygon points="2,16 15,3 28,16" fill="#cfd2d5"/></svg><div><h4>Easy Clean</h4><p class="body-text">Woven steel resists cuts and impact while staying light.</p></div></div>
      </article>
    </div>
  </section>

  <!-- Vacuum spread -->
  <section class="cell">
    <div class="spread">
      <article class="page left">
        <div class="ph" role="img" aria-label="Photo of a smiling family relaxing at home" style="left:60px;top:0;width:210px;height:70px;background:linear-gradient(180deg,#dfe7ef,#e9cdb8)"></div>
        <h2 class="title" style="left:14px;top:44px;font-size:12px">Ducted Vacuum</h2>
        <p class="body-text ph" style="left:14px;top:64px;width:110px">A ducted vacuum moves dust and allergens out of the living areas for a cleaner healthier home.</p>
        <div class="sub ph" style="left:14px;top:96px;width:120px;text-transform:none">No bags, less noise and no heavy machine to carry</div>
        <p class="body-text ph" style="left:14px;top:112px;width:110px">Simply plug the hose into a wall inlet and start cleaning.</p>
        <div class="ph" role="img" aria-label="Photo of vacuum hose and cleaning tool kit" style="left:140px;top:88px;width:120px;height:50px;background:linear-gradient(120deg,#f4f4f4,#9a9a9a)"></div>
      </article>
      <article class="page">
        <div class="ph" role="img" aria-label="Photo of a grey ducted vacuum power unit" style="left:20px;top:24px;width:80px;height:130px;background:linear-gradient(90deg,#3c4249,#5a6169,#3c4249);border-radius:6px"></div>
        <div class="ph" style="left:34px;top:58px;font-size:6px;font-weight:700;color:#fff">Cyclone Vac</div>
        <div class="ph" style="left:116px;top:24px;width:140px"><h4 class="sub" style="text-transform:none">Whisper Quiet Power</h4><p class="body-text">Power unit sits in the garage so rooms stay calm.</p></div>
        <div class="ph" style="left:116px;top:66px;width:140px"><h4 class="sub" style="text-transform:none">Cleaner Indoor Air</h4><p class="body-text">Power unit sits in the garage so rooms stay calm.</p></div>
        <div class="ph" style="left:116px;top:108px;width:140px"><h4 class="sub" style="text-transform:none">Why Choose Ducted</h4><p class="body-text">Power unit sits in the garage so rooms stay calm.</p></div>
      </article>
    </div>
  </section>

</main>
</body>
</html>
```